Brightwave Reach - Business Card

We need a business card for a Social Media Marketing company that specializes in online marketing for small businesses in Canada using common Social Media platforms such as Pixlora, Chatterly, Blinkpost & Quibber.

I have uploaded a copy of our logo which I would like utilized in the business card. We would like the business card to be modern yet classy design.

Our website is www.brightwavereach.ca

Industry/Entity Type

Marketing

Contact Information for Business Card

Email: info@brightwavereach.ca
Website: www.brightwavereach.ca
Telephone: 604-555-0193

Colors

Designer to choose colors to be used in the design.

Requirements
Must have
• Social Media icons on reverse
• Please add some designs with color.

```html
<!DOCTYPE html>
<html lang="en">
<head>
<meta charset="utf-8">
<title>Brightwave Reach – Business Card</title>
<link rel="stylesheet" href="https://fonts.googleapis.com/css2?family=Oswald:wght@500;600&family=Open+Sans:wght@400;600&display=swap">
<style>
  :root {
    --backdrop: #2b2b2b;
    --card: #efefef;
    --ink: #4a4c4e;
    --band: #3f4245;
    --band-text: #ffffff;
    --frame: #5a5c5e;
  }
  * { margin: 0; padding: 0; box-sizing: border-box; }
  html, body { width: 1200px; height: 960px; overflow: hidden; }
  body { background: var(--backdrop); position: relative; font-family: "Open Sans", Arial, sans-serif; }

  .card {
    position: absolute;
    width: 600px;
    height: 343px;
    background: var(--card);
    box-shadow: 0 3px 8px rgba(0,0,0,.5);
  }
  .card--front { left: 314px; top: 113px; }
  .card--back { left: 311px; top: 472px; }

  .front-frame {
    position: absolute;
    left: 16px; top: 12px;
    width: 570px; height: 318px;
    border: 4px solid var(--frame);
    border-radius: 3px;
  }
  .brand-name {
    position: absolute;
    left: 0; right: 0;
    text-align: center;
    font-family: "Oswald", "Arial Narrow", sans-serif;
    font-weight: 600;
    text-transform: uppercase;
    color: var(--ink);
    line-height: 1;
  }
  .card--front .brand-name { top: 60px; font-size: 30px; letter-spacing: .5px; }
  .card--back .brand-name { top: 122px; font-size: 36px; letter-spacing: .5px; }

  .contact-band {
    position: absolute;
    left: 15px; top: 192px;
    width: 571px; height: 138px;
    background: var(--band);
    border-radius: 0 0 4px 4px;
    color: var(--band-text);
  }
  .person { position: absolute; left: 49px; top: 44px; }
  .person-name {
    font-family: "Oswald", "Arial Narrow", sans-serif;
    font-weight: 500;
    font-size: 25px;
    line-height: 1.05;
    letter-spacing: .2px;
  }
  .person-role { font-size: 14.5px; margin-top: 2px; }

  .contact-list { position: absolute; left: 348px; top: 45px; list-style: none; }
  .contact-list li {
    display: flex; align-items: center;
    font-size: 14px; line-height: 19.5px;
  }
  .contact-list svg { width: 12px; height: 12px; margin-right: 9px; fill: var(--band-text); }

  .social-list {
    position: absolute;
    left: 0; right: 0; top: 282px;
    display: flex; justify-content: center; gap: 14px;
    list-style: none;
  }
  .social-list li {
    display: flex; align-items: center; gap: 5px;
    font-size: 12px; font-weight: 600; color: var(--ink);
  }
  .social-list .dot {
    width: 14px; height: 14px; border-radius: 50%;
    border: 1.5px solid var(--ink);
  }
</style>
</head>
<body>

<section class="card card--front" aria-label="Business card front">
  <div class="front-frame"></div>
  <div class="brand-name">Brightwave<br>Reach</div>
  <div class="contact-band">
    <div class="person">
      <div class="person-name">DANIEL REYES</div>
      <div class="person-role">CEO/FOUNDER</div>
    </div>
    <ul class="contact-list">
      <li>
        <svg viewBox="0 0 12 12" aria-hidden="true"><path d="M2.4 0.6l2 2.1-1 1.3c.7 1.5 2 2.8 3.6 3.6l1.3-1 2.1 2-1.2 1.9C4.7 10.2 1.5 6.9 0.5 1.8z"/></svg>
        604-555-0193
      </li>
      <li>
        <svg viewBox="0 0 12 12" aria-hidden="true"><path d="M0.5 2.5h11v7h-11z M0.5 2.5l5.5 4 5.5-4" fill="none" stroke="#fff" stroke-width="1.3"/><path d="M0.5 2.5h11L6 6.3z"/></svg>
        info@brightwavereach.ca
      </li>
      <li>
        <svg viewBox="0 0 12 12" aria-hidden="true"><circle cx="6" cy="6" r="5.5"/><path d="M3 3.5c1 .3 1.5 1 1.2 2s.8 1.5 1.6 1.3M7.5 1.5c-.3 1.2.7 1.8 1.8 1.5M7 10c0-1.2.8-2 2-2.2" fill="none" stroke="#3f4245" stroke-width="1"/></svg>
        www.brightwavereach.ca
      </li>
    </ul>
  </div>
</section>

<section class="card card--back" aria-label="Business card back">
  <div class="brand-name">Brightwave<br>Reach</div>
  <ul class="social-list">
    <li><span class="dot"></span>Chatterly</li>
    <li><span class="dot"></span>Pixlora</li>
    <li><span class="dot"></span>Quibber</li>
  </ul>
</section>

</body>
</html>
```